Residential Remodeling Contractor needs updated business card

I need a new design for my business card.
Name of the company is Ridgefell Construction. I need a card that commands presence, strength, integrity. I have been in business for 28 years. I am a Residential Remodeling Contractor that covers all aspects of a residential remodel and build.

```html
<!DOCTYPE html>
<html lang="en">
<head>
<meta charset="utf-8">
<title>Ridgefell Construction – Business Card</title>
<link rel="stylesheet" href="https://fonts.googleapis.com/css2?family=Cinzel:wght@600&family=Poppins:wght@400&display=swap">
<style>
  :root {
    --backdrop: #9b9b9b;
    --card-blue: #1f3d7d;
    --ink-white: #ffffff;
    --mark-blue: #5577d6;
    --card-shadow: rgba(0, 0, 0, 0.55);
  }
  * { margin: 0; padding: 0; box-sizing: border-box; }
  html, body {
    width: 1093px;
    height: 1200px;
    overflow: hidden;
    background: var(--backdrop);
  }
  .canvas {
    position: relative;
    width: 1093px;
    height: 1200px;
  }
  .card {
    position: absolute;
    left: 265px;
    width: 578px;
    height: 357px;
    background: var(--card-blue);
    border-radius: 26px;
    box-shadow: 3px 3px 3px var(--card-shadow);
    color: var(--ink-white);
  }
  .card--front { top: 226px; }
  .card--back  { top: 621px; width: 582px; }

  /* Front */
  .holder {
    position: absolute;
    left: 27px;
    top: 52px;
  }
  .holder__name {
    font-family: "Cinzel", serif;
    font-weight: 600;
    font-size: 23px;
    line-height: 23px;
    letter-spacing: 0.4px;
  }
  .holder__role {
    font-family: "Poppins", sans-serif;
    font-size: 17px;
    line-height: 20px;
  }
  .brand {
    position: absolute;
    right: 28px;
    top: 72px;
    display: flex;
    align-items: center;
    gap: 10px;
  }
  .brand__square {
    width: 14px;
    height: 14px;
    background: var(--ink-white);
  }
  .brand__name {
    font-family: "Poppins", sans-serif;
    font-weight: 400;
    font-size: 21px;
    line-height: 28px;
    color: var(--ink-white);
    white-space: nowrap;
  }
  .contacts {
    position: absolute;
    left: 27px;
    top: 252px;
    list-style: none;
    font-family: "Poppins", sans-serif;
    font-size: 17px;
    line-height: 21px;
  }
  .contacts li {
    display: flex;
    align-items: center;
    gap: 7px;
  }
  .contacts svg {
    width: 15px;
    height: 15px;
    flex: none;
    fill: none;
    stroke: var(--ink-white);
    stroke-width: 1.6;
  }
  .address {
    position: absolute;
    right: 28px;
    top: 273px;
    font-family: "Poppins", sans-serif;
    font-style: normal;
    font-size: 17px;
    line-height: 21px;
    text-align: right;
  }

  /* Back */
  .back-brand {
    position: absolute;
    inset: 0;
    display: flex;
    align-items: center;
    justify-content: center;
  }
  .back-brand__name {
    font-family: "Poppins", sans-serif;
    font-weight: 400;
    font-size: 38px;
    line-height: 46px;
    color: var(--mark-blue);
    white-space: nowrap;
  }
</style>
</head>
<body>
<main class="canvas">

  <section class="card card--front" aria-label="Business card front">
    <header class="holder">
      <h1 class="holder__name">DANIEL HARTLEY</h1>
      <p class="holder__role">Managing Director</p>
    </header>

    <div class="brand">
      <span class="brand__square"></span>
      <p class="brand__name">Ridgefell Construction</p>
    </div>

    <ul class="contacts">
      <li>
        <svg viewBox="0 0 16 16" aria-hidden="true"><path d="M3 1.5 L6 4.5 L4.5 6.5 Q6 10 9.5 11.5 L11.5 10 L14.5 13 L12.5 14.8 Q6 14 1.5 5 Z"/></svg>
        071-555 018 274
      </li>
      <li>
        <svg viewBox="0 0 16 16" aria-hidden="true"><rect x="1" y="3.5" width="14" height="9"/><path d="M1 3.5 L8 9 L15 3.5"/></svg>
        info@ridgefell.com
      </li>
      <li>
        <svg viewBox="0 0 16 16" aria-hidden="true"><circle cx="8" cy="8" r="6.5"/><ellipse cx="8" cy="8" rx="2.8" ry="6.5"/><path d="M1.5 8 H14.5 M2.5 5 H13.5 M2.5 11 H13.5"/></svg>
        www.ridgefellbuild.com
      </li>
    </ul>

    <address class="address">
      87, Harrow Mill Road<br>
      30718, Eastbrook Valley
    </address>
  </section>

  <section class="card card--back" aria-label="Business card back">
    <div class="back-brand">
      <p class="back-brand__name">Ridgefell Construction</p>
    </div>
  </section>

</main>
</body>
</html>
```